NZ First of it's kind solutions directory and marketplace for busy Mums needs a business card design

We need a business card design for our new nationwide business in NZ (long term plans to go global). We provide solutions to the everyday challenges that busy Mums face by connecting them with quality communities and suppliers of carefully selected, relevant products and services. We sell direct via our online marketplace. The final design should communicate our values of inclusivity, quality and smart solutions. Colours should incorporate our logo colour palette of #477077 and #6ba8b2. Our website is at https://www.brightnestmums.example

Target Market(s)

busy Mums, Age 28 – 50, female, income over $100K, location main centres NZ primarily but NZ wide. Is likely juggling work or career with a young family. Probably had hobbies which have fallen by the wayside.
-Wants to succeed in her chosen career without compromising on family life
-to successfully juggle her career without feeling like she is compromising her children
- Is time poor, something always has to give and it’s generally her health (she’ll stay up late, get stressed)
- probably ex corporate or professional career. Has discretional income

Industry/Entity Type

Business

Contact Information for Business Card

Lena Forbisher, Founder, BrightNestMums.example (Strapline Tap; Gather; Sorted), 47 Kowhai Terrace, Ellerslie, Auckland 1051, New Zealand. Mob: 021 483 517 Ph: +64 (0)9 571 4860

Font styles to use
Other font styles liked:
• Raleway, and/or Architects Daughter

Colors
00a990
33b8a4
86cfc6
cfeae6

Requirements
Must have
• the above details, streamline. the logo and colours associated with those logos
Should not have
• foil or metallic colours

```html
<!DOCTYPE html>
<html lang="en">
<head>
<meta charset="utf-8">
<title>BrightNestMums – Business Card</title>
<link rel="stylesheet" href="https://fonts.googleapis.com/css2?family=Arimo:wght@400;700&display=swap">
<style>
  :root {
    --brand-deep: #477077;
    --brand-light: #6ba8b2;
    --paper: #f8f8f8;
    --ink-white: #ffffff;
    --backdrop: #e9e6e3;
  }
  * { box-sizing: border-box; margin: 0; padding: 0; }
  html, body {
    width: 1200px; height: 900px; overflow: hidden;
    background: var(--backdrop);
    font-family: "Arimo", Arial, sans-serif;
  }
  .canvas { position: relative; width: 1200px; height: 900px; }

  .card { position: absolute; box-shadow: 0 6px 18px rgba(0,0,0,.18); overflow: hidden; }

  /* Front */
  .card--front {
    left: 177px; top: 74px; width: 590px; height: 364px;
    background: var(--brand-deep); color: var(--ink-white);
  }
  .brand-panel {
    position: absolute; left: 0; top: 0; width: 220px; height: 100%;
    background: var(--brand-light);
    display: flex; flex-direction: column; align-items: center; justify-content: center; gap: 16px;
  }
  .brand-panel__dot { width: 96px; height: 96px; border-radius: 50%; background: var(--ink-white); }
  .brand-panel__name { font-size: 18px; font-weight: 700; color: var(--ink-white); }

  .holder { position: absolute; right: 36px; top: 52px; text-align: right; }
  .holder__name { font-size: 22px; font-weight: 700; letter-spacing: .3px; }
  .holder__role { font-size: 16px; margin-top: 3px; }

  .contact { position: absolute; right: 36px; top: 189px; text-align: right; font-size: 16px; line-height: 22px; }
  .contact__line { display: flex; justify-content: flex-end; align-items: center; gap: 4px; }
  .contact__icon { width: 13px; height: 13px; fill: var(--ink-white); }
  .address { position: absolute; right: 36px; top: 256px; text-align: right; font-size: 16px; line-height: 22px; }

  /* Back */
  .card--back {
    left: 388px; top: 484px; width: 567px; height: 350px;
    background: var(--paper);
  }
  .wordmark {
    position: absolute; left: 0; right: 0; top: 146px;
    display: flex; justify-content: center; align-items: center; gap: 12px;
  }
  .wordmark__dot { width: 32px; height: 32px; border-radius: 50%; background: var(--brand-deep); }
  .wordmark__name { font-size: 34px; font-weight: 700; color: var(--brand-deep); }
  .web-address {
    position: absolute; left: 0; right: 0; top: 280px; text-align: center;
    font-size: 15px; font-weight: 700; color: var(--brand-deep);
  }
  .web-address__domain { color: var(--brand-light); }
</style>
</head>
<body>
<main class="canvas">
  <section class="card card--front" aria-label="Business card front">
    <div class="brand-panel">
      <span class="brand-panel__dot"></span>
      <span class="brand-panel__name">BrightNestMums</span>
    </div>

    <div class="holder">
      <p class="holder__name">LENA FORBISHER</p>
      <p class="holder__role">Founder</p>
    </div>

    <div class="contact">
      <p class="contact__line">021 483 517
        <svg class="contact__icon" viewBox="0 0 16 16" aria-hidden="true"><path d="M2 5c0-2 2-3 6-3s6 1 6 3v1h-3V5H5v1H2zM4 8l2-2h4l2 2v5H4zm4 1.5a1.5 1.5 0 1 0 0 3 1.5 1.5 0 0 0 0-3z"/></svg>
      </p>
      <p class="contact__line">+64 (0)9 571 4860
        <svg class="contact__icon" viewBox="0 0 16 16" aria-hidden="true"><path d="M4 1h8a1 1 0 0 1 1 1v12a1 1 0 0 1-1 1H4a1 1 0 0 1-1-1V2a1 1 0 0 1 1-1zm1 2v9h6V3z"/></svg>
      </p>
      <p class="contact__line">www.BrightNestMums.example
        <svg class="contact__icon" viewBox="0 0 16 16" aria-hidden="true"><circle cx="8" cy="8" r="7"/><path d="M5 5l2 1 1 2-2 1-1 3M10 3l1 2 2 1M10 11l1-2 2 1" stroke="#477077" stroke-width="1.3" fill="none"/></svg>
      </p>
    </div>

    <div class="address">
      <p>47 Kowhai Terrace, Ellerslie</p>
      <p>Auckland 1051, New Zealand</p>
    </div>
  </section>

  <section class="card card--back" aria-label="Business card back">
    <div class="wordmark">
      <span class="wordmark__dot"></span>
      <span class="wordmark__name">BrightNestMums</span>
    </div>
    <p class="web-address">www.<span class="web-address__domain">BrightNestMums</span>.example</p>
  </section>
</main>
</body>
</html>
```